Banner Pop Up Opt In Form REDESIGNS - SLEEK BLACK LOOK

Please redesign banners attached.

I am looking for a very sleek look....I do not like this collage of images on these current designs. Please keep all content same but use images that pop.

I have an acccount at www.pixvane-example.com or you can use your own images.

I like black background for somereason because it looks very sleek....but these designs should pop , build trust and credibility and have easy opt in form....SLEEK AND MODERN LOOK is what im looking for....

Target Market(s)

Consumers on websites

Requirements
Must have
• Please redesign banners attached.

Nice to have

Should not have

```html
<!DOCTYPE html>
<html lang="en">
<head>
<meta charset="utf-8">
<title>Newsletter Opt-In Banners</title>
<link rel="stylesheet" href="https://fonts.googleapis.com/css2?family=Questrial&family=Pathway+Gothic+One&display=swap">
<style>
  :root {
    --bg-deep: #0a0a0a;
    --bg-mid: #1b1b1b;
    --divider: #9a9a9a;
    --gold-light: #fff2b0;
    --gold-mid: #d9ad3c;
    --gold-dark: #8a6514;
    --gold-text: #d8b04a;
    --green-text: #5a9c1a;
    --green-light: #9be04a;
    --green-dark: #3f8a10;
    --field: #ffffff;
    --ink: #111111;
    --footer-text: #f2f2f2;
    --plate-dark: #2a2320;
    --plate-food: #b06a2c;
  }
  html, body {
    margin: 0;
    padding: 0;
    width: 1200px;
    height: 516px;
    overflow: hidden;
    background: var(--bg-deep);
  }
  .canvas {
    position: relative;
    width: 1200px;
    height: 516px;
    display: flex;
  }
  .banner {
    position: relative;
    width: 600px;
    height: 516px;
    overflow: hidden;
    background: radial-gradient(ellipse at 50% 35%, var(--bg-mid) 0%, var(--bg-deep) 75%);
  }
  .divider {
    width: 1px;
    height: 516px;
    background: var(--divider);
  }
  .banner--win { width: 599px; }
  .headline {
    position: absolute;
    left: 0;
    width: 100%;
    margin: 0;
    text-align: center;
    font-family: "Questrial", sans-serif;
    font-weight: 400;
    line-height: 1;
    white-space: nowrap;
    background: linear-gradient(180deg, var(--gold-light) 0%, var(--gold-mid) 45%, var(--gold-dark) 60%, var(--gold-mid) 80%, var(--gold-light) 100%);
    -webkit-background-clip: text;
    background-clip: text;
    color: transparent;
  }
  .headline__line { display: block; }
  .banner--offer .headline { top: 10px; font-size: 84px; letter-spacing: -2px; }
  .banner--offer .headline__line + .headline__line { margin-top: -12px; }
  .banner--win .headline { top: 22px; font-size: 86px; letter-spacing: -1px; }
  .pitch {
    position: absolute;
    left: 0;
    width: 100%;
    margin: 0;
    text-align: center;
    font-family: "Pathway Gothic One", sans-serif;
    font-size: 21px;
    line-height: 22px;
    color: var(--gold-text);
    letter-spacing: 0.2px;
  }
  .pitch__prize { display: block; color: var(--green-text); }
  .banner--offer .pitch { top: 170px; }
  .banner--win .pitch { top: 126px; }
  .optin {
    position: absolute;
    width: 268px;
  }
  .banner--offer .optin { left: 33px; top: 243px; }
  .banner--win .optin { left: 32px; top: 206px; }
  .optin__field {
    display: block;
    box-sizing: border-box;
    width: 268px;
    height: 43px;
    margin: 0 0 17px;
    background: var(--field);
    border: 3px solid var(--gold-mid);
    border-top-color: var(--gold-light);
    box-shadow: inset 0 0 0 1px var(--gold-dark);
  }
  .banner--offer .optin__field { margin-bottom: 17px; }
  .banner--win .optin__field { margin-bottom: 19px; }
  .optin__submit {
    position: absolute;
    width: 114px;
    height: 33px;
    border: 1px solid var(--green-dark);
    background: linear-gradient(180deg, var(--green-light) 0%, var(--green-dark) 100%);
    font-family: "Pathway Gothic One", sans-serif;
    font-size: 24px;
    color: var(--ink);
    padding: 0;
    line-height: 31px;
  }
  .banner--offer .optin__submit { left: 70px; top: 179px; }
  .banner--win .optin__submit { left: 72px; top: 179px; }
  .dish {
    position: absolute;
    width: 238px;
    height: 238px;
    border-radius: 50%;
    background: radial-gradient(circle at 50% 50%, var(--plate-food) 0%, #7a4a24 45%, var(--plate-dark) 72%, #151210 100%);
  }
  .banner--offer .dish { left: 331px; top: 230px; }
  .banner--win .dish { left: 331px; top: 193px; }
  .notice {
    position: absolute;
    left: 35px;
    top: 490px;
    margin: 0;
    font-family: "Questrial", sans-serif;
    font-size: 10.5px;
    color: var(--footer-text);
    white-space: nowrap;
  }
</style>
</head>
<body>
<div class="canvas">
  <section class="banner banner--offer">
    <h1 class="headline"><span class="headline__line">WANT A</span><span class="headline__line">GREAT OFFER?</span></h1>
    <p class="pitch">SUBSCRIBE TO OUR NEWSLETTER AND RECEIVE A COMPLIMENTARY<span class="pitch__prize">$300 RESTAURANT CERTIFICATE</span></p>
    <form class="optin">
      <input class="optin__field" type="text" aria-label="Name">
      <input class="optin__field" type="email" aria-label="Email">
      <input class="optin__field" type="tel" aria-label="Phone">
      <button class="optin__submit" type="button">SUBMIT</button>
    </form>
    <div class="dish" role="img" aria-label="Grilled steak with roasted potato wedges and rosemary on a dark plate"></div>
    <p class="notice">WE WILL SEND AN EMAIL AND A TEXT MESAGE WITH THE OFFER AND HOW TO REDEEM</p>
  </section>
  <div class="divider"></div>
  <section class="banner banner--win">
    <h1 class="headline"><span class="headline__line">ENTER TO WIN!</span></h1>
    <p class="pitch">SUBSCRIBE TO OUR NEWSLETTER AND RECEIVE A COMPLIMENTARY<span class="pitch__prize">$300 RESTAURANT CERTIFICATE</span></p>
    <form class="optin">
      <input class="optin__field" type="text" aria-label="Name">
      <input class="optin__field" type="email" aria-label="Email">
      <input class="optin__field" type="tel" aria-label="Phone">
      <button class="optin__submit" type="button">SUBMIT</button>
    </form>
    <div class="dish" role="img" aria-label="Grilled steak with roasted potato wedges and rosemary on a dark plate"></div>
    <p class="notice">WE WILL SEND AN EMAIL AND A TEXT MESAGE WITH THE OFFER AND HOW TO REDEEM</p>
  </section>
</div>
</body>
</html>
```